Birchline Septic Solutions

Would like to see some single sided ones but would also like to see some double sided with one sided only being the logo. Owners name is Colin Vandro. Phone number is 555-214-0387
Services are pumping, inspections, installs, and repairs

Contact Information for Business Card

555-241-0387 Colin Vandro Harlowbrook, OH

```html
<!DOCTYPE html>
<html lang="en">
<head>
<meta charset="utf-8">
<title>Birchline Septic Solutions – Business Cards</title>
<link href="https://fonts.googleapis.com/css2?family=Montserrat:wght@400;500;700;800&display=swap" rel="stylesheet">
<style>
  :root {
    --ink: #0b0b0b;
    --paper: #ffffff;
    --teal: #2bbcb3;
    --grey: #3a3a3a;
    --backdrop: #d9d9d9;
  }
  * { box-sizing: border-box; margin: 0; padding: 0; }
  html, body { width: 1200px; height: 880px; overflow: hidden; }
  body {
    background: var(--backdrop);
    font-family: "Montserrat", sans-serif;
    position: relative;
  }
  .card {
    position: absolute;
    width: 560px;
    height: 320px;
    border-radius: 4px;
    overflow: hidden;
    box-shadow: 0 10px 28px rgba(0,0,0,0.25);
  }
  .card-front { left: 120px; top: 110px; background: var(--ink); color: var(--paper); }
  .card-back { left: 520px; top: 450px; background: var(--paper); color: var(--ink); }

  .wordmark {
    font-weight: 800;
    text-transform: uppercase;
    letter-spacing: 0.04em;
    line-height: 1.1;
    display: flex;
    align-items: center;
    gap: 12px;
  }
  .wordmark-dot { width: 16px; height: 16px; border-radius: 50%; background: var(--teal); flex: none; }

  .card-front .wordmark {
    position: absolute; left: 0; right: 0; top: 70px;
    justify-content: center; font-size: 32px; color: var(--paper);
  }
  .services {
    position: absolute; left: 0; right: 0; top: 190px;
    text-align: center; font-size: 19px; font-weight: 400; line-height: 1.55;
  }
  .tick { width: 16px; height: 16px; vertical-align: -2px; margin: 0 5px; }

  .back-swoosh { position: absolute; inset: 0; }
  .card-back .wordmark {
    position: absolute; left: 36px; top: 118px; width: 240px;
    font-size: 21px; color: var(--ink);
  }
  .divider {
    position: absolute; left: 286px; top: 70px; width: 2px; height: 120px; background: var(--teal);
  }
  .contact { position: absolute; left: 306px; top: 62px; font-size: 14px; line-height: 1.4; }
  .contact-name { font-size: 20px; font-weight: 800; text-transform: uppercase; letter-spacing: 0.01em; }
  .contact-name .surname { color: var(--teal); }
  .contact-role { font-size: 14px; margin-bottom: 8px; }
  .phone-row { display: flex; align-items: center; gap: 6px; }
  .phone-icon { width: 14px; height: 14px; }
</style>
</head>
<body>

<section class="card card-front" aria-label="Front of business card">
  <div class="wordmark"><span class="wordmark-dot"></span>Birchline<br>Septic Solutions</div>
  <p class="services">
    <svg class="tick" viewBox="0 0 16 16"><circle cx="8" cy="8" r="6.5" fill="none" stroke="currentColor" stroke-width="1.6"/><path d="M5 8.3l2 2 4-4.3" fill="none" stroke="currentColor" stroke-width="1.6"/></svg>Services are pumping<br>
    <svg class="tick" viewBox="0 0 16 16"><circle cx="8" cy="8" r="6.5" fill="none" stroke="currentColor" stroke-width="1.6"/><path d="M5 8.3l2 2 4-4.3" fill="none" stroke="currentColor" stroke-width="1.6"/></svg>inspections
    <svg class="tick" viewBox="0 0 16 16"><circle cx="8" cy="8" r="6.5" fill="none" stroke="currentColor" stroke-width="1.6"/><path d="M5 8.3l2 2 4-4.3" fill="none" stroke="currentColor" stroke-width="1.6"/></svg>installs
    <svg class="tick" viewBox="0 0 16 16"><circle cx="8" cy="8" r="6.5" fill="none" stroke="currentColor" stroke-width="1.6"/><path d="M5 8.3l2 2 4-4.3" fill="none" stroke="currentColor" stroke-width="1.6"/></svg>and repairs
  </p>
</section>

<section class="card card-back" aria-label="Back of business card">
  <svg class="back-swoosh" viewBox="0 0 560 320" preserveAspectRatio="none">
    <path d="M300 320 Q470 290 560 130 L560 320 Z" fill="var(--ink)"/>
    <path d="M150 306 Q440 292 540 150" fill="none" stroke="var(--teal)" stroke-width="4" stroke-linecap="round"/>
  </svg>
  <div class="wordmark"><span class="wordmark-dot"></span>Birchline<br>Septic Solutions</div>
  <div class="divider"></div>
  <div class="contact">
    <p class="contact-name">Colin <span class="surname">Vandro</span></p>
    <p class="contact-role">Owners</p>
    <p>555-214-0387</p>
    <p class="phone-row">
      <svg class="phone-icon" viewBox="0 0 16 16"><path d="M3 2h3l1.5 3.5-2 1.3a8 8 0 0 0 3.7 3.7l1.3-2L14 10v3a1 1 0 0 1-1 1A11 11 0 0 1 2 3a1 1 0 0 1 1-1z" fill="var(--teal)"/></svg>
      555-241-0387 Colin
    </p>
    <p>Vandro Harlowbrook, OH</p>
  </div>
</section>

</body>
</html>
```